Soy Candle Labels

We sell soy candles in recycled wine bottles. The wine bottle is cut in half and filled with pure and natural soy wax and scented with essential oils.
Our product represents good use of up cycling materials for a better use. The product is all natural and eco friendly.
You can see good use of labels and branding for a company in America that does the same thing http://larkmeadow7wicks.example/
Trya dn keep the label uncomplicated like the above labels.
We will need an area to hand stamp the scent. Similar to the labels used on the above website.
We would prefer to use a white or off white paper label with gold or bronze printing - limit the use of colour and keep the label simple and sophisticated.
Emberlace Candle Co. is our company name. Emberlace being the predominant name and candle co. written small underneath right justified.
Die cut labels might look better than a rectangle.
Dimensions should be 90mm Wide x 90mm High
The final design should communicate a professional and quality product. But stay modern and professional. Clean, elegant and sophisticated.
Can use wording such as: Hand Poured, Premium Soy Wax, All Natural, Up cycled
Have a look at the attached image for the look and feel we are going for.
Updates
Designers are having a little bit of trouble interpreting the brief into a viable design. To assist perhaps you can look at WINE LABELS on google images. Design your label around an existing style wine label to give the canld ethe feel of being a bottle of wine. Get creative! :)
Reason: We require more designs. We havnt quite got what were looking for.
Please see brief.

```html
<!DOCTYPE html>
<html lang="en">
<head>
<meta charset="utf-8">
<title>Emberlace Candle Co. – Soy Candle Label</title>
<link rel="stylesheet" href="https://fonts.googleapis.com/css2?family=Ropa+Sans&family=Pathway+Gothic+One&display=swap">
<style>
  :root {
    --backdrop: #3a302e;
    --paper: #fcfbf6;
    --ink: #3b302d;
  }
  * { margin: 0; padding: 0; box-sizing: border-box; }
  html, body {
    width: 1200px;
    height: 1000px;
    overflow: hidden;
    background: var(--backdrop);
  }
  .canvas {
    position: relative;
    width: 1200px;
    height: 1000px;
  }
  .label {
    position: absolute;
    left: 150px;
    top: 53px;
    width: 903px;
    height: 905px;
    background: var(--paper);
    border-radius: 22px;
  }
  .label-frame {
    position: absolute;
    left: 14px;
    top: 16px;
    width: 873px;
    height: 873px;
    border: 1.5px solid var(--ink);
    border-radius: 18px;
  }
  .claims {
    position: absolute;
    left: 43px;
    top: 42px;
    color: var(--ink);
    font-family: "Ropa Sans", sans-serif;
  }
  .claims-title {
    font-size: 41px;
    line-height: 48px;
  }
  .claims-line {
    font-size: 28px;
    line-height: 38px;
  }
  .brand {
    position: absolute;
    right: 50px;
    top: 390px;
    text-align: right;
    color: var(--ink);
    font-family: "Ropa Sans", sans-serif;
    font-weight: 400;
  }
  .brand-name {
    font-size: 136px;
    line-height: 150px;
  }
  .brand-tagline {
    font-size: 32px;
    line-height: 40px;
    margin-right: 22px;
  }
  .ornament-band {
    position: absolute;
    left: 15px;
    top: 642px;
    width: 872px;
    height: 96px;
    background: linear-gradient(180deg, #e6e1da 0%, #8f8580 50%, #e6e1da 100%);
  }
  .footer-note {
    position: absolute;
    top: 786px;
    display: flex;
    align-items: center;
    gap: 16px;
    color: var(--ink);
    font-family: "Pathway Gothic One", sans-serif;
    font-size: 48px;
    line-height: 60px;
  }
  .footer-note--origin { left: 43px; }
  .footer-note--material { right: 42px; }
  .flourish {
    display: flex;
    align-items: center;
    gap: 6px;
  }
  .flourish-rule {
    width: 2px;
    height: 52px;
    background: var(--ink);
  }
  .flourish-mark {
    width: 56px;
    height: 30px;
    border-radius: 15px;
    background: #b8b0aa;
  }
</style>
</head>
<body>
<main class="canvas">
  <section class="label">
    <div class="label-frame"></div>

    <div class="claims">
      <p class="claims-title">Hand Poured</p>
      <p class="claims-line">All Natural Soy</p>
      <p class="claims-line">320 gm of Premium Soy Wax</p>
    </div>

    <div class="brand">
      <p class="brand-name">Emberlace</p>
      <p class="brand-tagline">Candle Co.</p>
    </div>

    <div class="ornament-band" role="img" aria-label="Decorative engraved scroll border with repeating rosettes"></div>

    <p class="footer-note footer-note--origin">
      <span>Product of Australia</span>
      <span class="flourish">
        <span class="flourish-rule"></span>
        <span class="flourish-mark" role="img" aria-label="Small scroll flourish"></span>
      </span>
    </p>

    <p class="footer-note footer-note--material">
      <span class="flourish">
        <span class="flourish-mark" role="img" aria-label="Small scroll flourish"></span>
        <span class="flourish-rule"></span>
      </span>
      <span>up-cycled wine bottle</span>
    </p>
  </section>
</main>
</body>
</html>
```